Redesign Website - Current one too plain

The description is in the uploaded file. Please let me know if you need any more information. I'd prefer it if someone could implement the design to a WordPress site but the best design will win, regardless.
I would like the forms to look nice as well
UPDATE:
I don't think we can use the images that I provided, I think they make the site look a bit 'cheap' and I really don't know how to replace them. One thought I have had is to make the "Simple, Unique, Effective" a second feature on the right side of the page with the search on the left
Target Market(s)
Small companies, private sellers of cars and people who rent their caravan/holiday home out
Industry/Entity Type
Advertising
Number of Pages Required
3 page
Colors
Designer to choose colors to be used in the design.
Look and feel
Each slider illustrates characteristics of the customer's brand and the style your logo design should communicate.

```html
<!DOCTYPE html>
<html lang="en">
<head>
<meta charset="UTF-8">
<title>Discover And Connect</title>
<link href="https://fonts.googleapis.com/css2?family=Inter:wght@400;500;600&display=swap" rel="stylesheet">
<style>
  :root {
    --bg: #242424;
    --text: #ffffff;
    --accent: #e8fa55;
    --accent-ink: #1e1e1e;
    --photo-top: #2e3035;
    --photo-mid: #4a4e55;
    --photo-low: #6e737b;
  }
  * { margin: 0; padding: 0; box-sizing: border-box; }
  html, body { width: 1200px; height: 853px; overflow: hidden; }
  body {
    background: var(--bg);
    font-family: "Inter", Arial, sans-serif;
    color: var(--text);
    position: relative;
  }
  .main-nav a {
    position: absolute;
    top: 63px;
    font-size: 13.5px;
    color: var(--text);
    text-decoration: none;
    transform: translateX(-50%);
  }
  .hero-title {
    position: absolute;
    top: 138px;
    left: 0;
    width: 1200px;
    text-align: center;
    font-size: 58px;
    font-weight: 600;
    letter-spacing: 0.2px;
  }
  .hero-subtitle {
    position: absolute;
    top: 222px;
    left: 0;
    width: 1200px;
    text-align: center;
    font-size: 16.5px;
    font-weight: 400;
    letter-spacing: 0.15px;
  }
  .code-picker {
    position: absolute;
    top: 292px;
    width: 70px;
    transform: translateX(-50%);
    display: flex;
    flex-direction: column;
    align-items: center;
    color: var(--accent);
  }
  .code-picker .char {
    font-size: 86px;
    font-weight: 500;
    line-height: 84px;
  }
  .code-picker svg { display: block; }
  .type-chip {
    position: absolute;
    top: 439px;
    height: 33px;
    border: 1px solid var(--accent);
    border-radius: 17px;
    color: var(--accent);
    font-size: 17px;
    display: flex;
    align-items: center;
    justify-content: center;
    background: transparent;
    font-family: inherit;
  }
  .search-button {
    position: absolute;
    top: 499px;
    left: 481px;
    width: 237px;
    height: 37px;
    border: none;
    border-radius: 19px;
    background: var(--accent);
    color: var(--accent-ink);
    font-family: inherit;
    font-size: 17px;
  }
  .vehicle-photo {
    position: absolute;
    left: 0;
    top: 572px;
    width: 1200px;
    height: 281px;
    background: linear-gradient(180deg, var(--photo-top) 0%, var(--photo-mid) 60%, var(--photo-low) 100%);
  }
</style>
</head>
<body>
  <nav class="main-nav">
    <a href="#" style="left:442px">Home</a>
    <a href="#" style="left:531px">Advertise</a>
    <a href="#" style="left:631px">Contact</a>
    <a href="#" style="left:738px">Register</a>
  </nav>

  <h1 class="hero-title">Discover And Connect</h1>
  <p class="hero-subtitle">Display Your Unique Code on Your Vehicle to Attract Customers</p>

  <div class="code-picker" style="left:546px">
    <svg width="17" height="17" viewBox="0 0 17 17"><circle cx="8.5" cy="8.5" r="8.5" fill="var(--accent)"/><path d="M5 10 L8.5 6.5 L12 10" fill="none" stroke="var(--accent-ink)" stroke-width="1.6" stroke-linecap="round"/></svg>
    <span class="char">S</span>
    <svg width="17" height="17" viewBox="0 0 17 17"><circle cx="8.5" cy="8.5" r="8.5" fill="var(--accent)"/><path d="M5 7 L8.5 10.5 L12 7" fill="none" stroke="var(--accent-ink)" stroke-width="1.6" stroke-linecap="round"/></svg>
  </div>
  <div class="code-picker" style="left:631px">
    <svg width="17" height="17" viewBox="0 0 17 17"><circle cx="8.5" cy="8.5" r="8.5" fill="var(--accent)"/><path d="M5 10 L8.5 6.5 L12 10" fill="none" stroke="var(--accent-ink)" stroke-width="1.6" stroke-linecap="round"/></svg>
    <span class="char">6</span>
    <svg width="17" height="17" viewBox="0 0 17 17"><circle cx="8.5" cy="8.5" r="8.5" fill="var(--accent)"/><path d="M5 7 L8.5 10.5 L12 7" fill="none" stroke="var(--accent-ink)" stroke-width="1.6" stroke-linecap="round"/></svg>
  </div>

  <button class="type-chip" style="left:439px;width:55px">Car</button>
  <button class="type-chip" style="left:529px;width:93px">Caravan</button>
  <button class="type-chip" style="left:657px;width:104px">Company</button>

  <button class="search-button">Search</button>

  <div class="vehicle-photo" role="img" aria-label="Photo of a dark grey sports car seen from the front"></div>
</body>
</html>
```